Wordpress Design Project SEO/SEM Website

Need an updated more professional look for an SEO/SEM existing site.
see: www.brightquill-hub.com

I have an existing logo (in eps format), but am flexible on color and would consider updating the logo if the current colors or design limits your creativity.

Target Market(s)

My customers tend to be marketing managers for mid-size companies with 50+ employees.

Industry/Entity Type

Marketing

Requirements
Must have
• Design should support WordPress 3.0 menus, and widgets.
Nice to have
• Should you want/need it, the font used in the logo is 'ARTLOOKIN'
Should not have
• flash

```html
<!DOCTYPE html>
<html lang="en">
<head>
<meta charset="utf-8">
<title>Brightquill Hub – Internet Marketing</title>
<link href="https://fonts.googleapis.com/css2?family=Ubuntu:wght@300;400;500&display=swap" rel="stylesheet">
<style>
:root{
  --teal:#0b6a8e;
  --teal-dark:#085673;
  --heading:#14668a;
  --accent:#1d9fd6;
  --ink:#3a3a3a;
  --panel:#e9e9e9;
  --side:#ebebeb;
  --rule:#d4d4d4;
  --white:#ffffff;
}
*{box-sizing:border-box;margin:0;padding:0}
html,body{width:1040px;height:1200px;overflow:hidden}
body{position:relative;background:var(--white);font-family:'Ubuntu',sans-serif;color:var(--ink)}
.abs{position:absolute}

.brand{left:40px;top:8px;width:120px;height:125px;text-align:center;z-index:2}
.brand-dot{width:44px;height:44px;border-radius:50%;background:var(--teal);margin:30px auto 0}
.brand-name{position:absolute;left:0;right:0;top:102px;color:var(--white);font-weight:300;font-size:22px;letter-spacing:3px}

.search{left:672px;top:53px;width:338px;height:48px;background:var(--teal);box-shadow:0 2px 6px rgba(0,0,0,.3)}
.search-field{position:absolute;left:12px;top:12px;width:280px;height:26px;background:var(--white);border:2px solid #cfd6da}
.search-btn{position:absolute;left:298px;top:10px}

.navbar{left:0;top:101px;width:1040px;height:46px;background:linear-gradient(#111d23,#02090c)}
.nav{position:absolute;top:9px;left:309px;display:flex;list-style:none}
.nav li{font-size:15px;color:var(--white);height:28px;line-height:28px;margin-right:36px}
.nav li.active{background:linear-gradient(#2aa9e0,#0a7cb6);border-radius:14px;width:95px;text-align:center;margin-right:40px}
.nav li:nth-child(2){width:87px}
.nav li:nth-child(3){width:60px}
.nav li:nth-child(4){width:61px}
.nav li:nth-child(5){width:94px}

.band{left:0;top:147px;width:1040px;height:378px;background:var(--teal)}

.hero{left:31px;top:201px;width:680px;height:359px;background:var(--panel)}
.hero h1{position:absolute;left:31px;top:38px;font-weight:500;font-size:47px;line-height:53px;color:var(--heading);letter-spacing:1px}
.hero h2{position:absolute;left:31px;top:152px;font-weight:400;font-size:21px;color:#222}
.hero p{position:absolute;left:31px;top:178px;width:305px;font-size:13px;line-height:22px;color:#555;letter-spacing:.2px}
.hero-visual{position:absolute;left:362px;top:45px;width:278px;height:295px;border-radius:4px;background:linear-gradient(160deg,#f4f4f4 0%,#d9dde0 45%,#a9c8d8 70%,#c9c9c9 100%)}
.btn{display:block;text-align:center;color:var(--white);background:linear-gradient(#27a7de,#0a72aa);border-radius:14px;font-size:14px}
.hero .btn{position:absolute;left:218px;top:307px;width:109px;height:26px;line-height:26px}

.portrait{left:870px;top:155px;width:140px;height:126px;background:linear-gradient(#1b7a9c,#3d2e25 70%,#0d0d0d)}

.cta{left:723px;top:281px;width:289px;height:280px;background:linear-gradient(#0c2732,#020608)}
.cta h3{position:absolute;left:17px;top:18px;font-weight:500;font-size:24px;line-height:25px;color:var(--accent)}
.cta p{position:absolute;left:17px;width:245px;font-size:11px;line-height:16px;color:#e6e6e6;letter-spacing:.2px}
.cta strong{font-weight:500;color:var(--white)}
.cta .btn{position:absolute;left:70px;top:228px;width:147px;height:32px;line-height:32px;font-weight:500;color:#062030}

.widget{left:723px;width:289px;background:var(--side)}
.widget h4{position:absolute;left:31px;font-weight:400;font-size:15px;color:#111}
.cats{position:absolute;left:31px;top:54px;width:235px;list-style:none;border-top:1px solid var(--rule)}
.cats li{height:35px;line-height:34px;border-bottom:1px solid var(--rule);font-size:11px;color:var(--teal);padding-left:35px;position:relative}
.cats li::before{content:"";position:absolute;left:8px;top:13px;width:8px;height:8px;border-radius:50%;background:#111}
.badge{position:absolute;left:49px;top:215px;width:168px;height:38px;background:linear-gradient(#dcdcdc,#a9a9a9);border:1px solid #999}
.field-label{position:absolute;left:29px;font-size:12px;color:var(--teal)}
.field{position:absolute;left:29px;width:232px;height:26px;background:var(--white);border-top:2px solid #999}
.remember{position:absolute;left:31px;top:166px;font-size:12px;color:#666;display:flex;align-items:center}
.remember span{width:10px;height:10px;border:1px solid #aaa;margin-right:8px;background:#fafafa}
.login-btn{position:absolute;left:181px;top:161px;width:80px;height:23px;line-height:23px;border-radius:12px;background:#050505;color:var(--white);text-align:center;font-size:13px}

.share{left:743px;top:1062px;display:flex;align-items:center;font-size:12px;font-weight:500;color:#111}
.share span{margin-right:14px;letter-spacing:.3px}
.share i{display:block;width:20px;height:20px;margin-right:7px;border-radius:2px}

.content{left:32px;top:594px;width:677px}
.content h5{font-weight:500;font-size:14px;color:var(--teal-dark);margin-bottom:6px}
.content p{font-size:12.8px;line-height:18px;color:#444;margin-bottom:16px}
.content p.tight{margin-bottom:7px}

.footer{left:0;top:1095px;width:1040px;height:105px;background:linear-gradient(#0e1b21,#02090c);text-align:center;color:#ddd;font-size:10px;line-height:17px;padding-top:53px}
</style>
</head>
<body>

<div class="abs navbar">
  <ul class="nav">
    <li class="active">Home</li>
    <li>Services</li>
    <li>SEO</li>
    <li>SEM</li>
    <li>About Us</li>
    <li>Contact Us</li>
  </ul>
</div>

<div class="abs brand">
  <div class="brand-dot"></div>
  <div class="brand-name">BQH</div>
</div>

<div class="abs search">
  <div class="search-field"></div>
  <svg class="search-btn" width="30" height="28" viewBox="0 0 30 28">
    <circle cx="11" cy="11" r="7.5" fill="none" stroke="#fff" stroke-width="3"/>
    <line x1="16.5" y1="16.5" x2="26" y2="25" stroke="#fff" stroke-width="4" stroke-linecap="round"/>
  </svg>
</div>

<div class="abs band"></div>

<section class="abs hero">
  <h1>Brightquill<br>Hub</h1>
  <h2>Internet Marketing</h2>
  <p>Brightquill Hub provides Search Engine Optimization (SEO) and Search Engine Marketing (SEM) services for the Huntsville Alabama area. Our focus is optimizing and marketing websites to maximize results.</p>
  <div class="hero-visual" role="img" aria-label="Illustration of a sphere covered in marketing keywords"></div>
  <a class="btn">Read more</a>
</section>

<div class="abs portrait" role="img" aria-label="Portrait photo of the consultant"></div>

<aside class="abs cta">
  <h3>Need Help with<br>Internet Marketing?</h3>
  <p style="top:88px">We provide SEO and SEM services to a wide range of companies and welcome the opportunity to discuss your needs.</p>
  <p style="top:141px">If you are trying to drive more traffic to your web site, generate more leads, and convert more of those leads into sales – <strong>Contact Us Now!</strong></p>
  <a class="btn">Contact Us Now !</a>
</aside>

<aside class="abs widget" style="top:564px;height:278px">
  <h4 style="top:28px">Posts by Category</h4>
  <ul class="cats">
    <li>SEM Huntsville (44)</li>
    <li>SEO Huntsville (46)</li>
    <li>Web Analytics (10)</li>
  </ul>
  <h4 style="top:186px">Member</h4>
  <div class="badge"></div>
</aside>

<aside class="abs widget" style="top:846px;height:204px">
  <h4 style="top:16px">Login</h4>
  <div class="field-label" style="top:50px">Username</div>
  <div class="field" style="top:65px"></div>
  <div class="field-label" style="top:106px">Password</div>
  <div class="field" style="top:121px"></div>
  <div class="remember"><span></span>Remember me</div>
  <div class="login-btn">Login</div>
</aside>

<div class="abs share">
  <span>Share this :</span>
  <i style="background:#c9d6e0"></i>
  <i style="background:#3b5a97"></i>
  <i style="background:#41a8d5"></i>
  <i style="background:#1c6da3"></i>
  <i style="background:#f18a1f"></i>
</div>

<main class="abs content">
  <h5>Quality Content</h5>
  <p>Your site’s content must convey its purpose in a clear fashion and, within seconds, convince your visitors that they have found something worth further exploration. In order for the search engine to target your content, however, the copy must contain key phrases that can be married to the searchers’ requests.</p>
  <h5>Site Architecture</h5>
  <p>The architecture of your site should convey in hierarchical fashion the relationship and importance of your content. Also, it is imperative to have clear navigation that helps your visitors to locate the information they are seeking, that informs your visitors where they currently are on your site, and that is intuitive to use.</p>
  <h5>Incoming Links</h5>
  <p>The quality and quantity of incoming links are at the core of Searchly’s Page Rank algorithm. Incoming links can come from many sources, including blogs, forums, social networking sites, and press releases. Theses links serve as “votes” that signal the importance and relevance of your content to search engines.</p>
  <h5>Freshness</h5>
  <p class="tight">The freshness (or recency) of your content is also a factor in how your content ranks in the search results. This means that businesses that routinely update the content of their website will rank higher in the search results than websites that rarely change.</p>
  <p>Brightquill Hub focuses on analyzing, optimizing, and marketing websites to maximize results. We can provide an initial Website Audit to evaluate the architecture of your website, the quality of your content, and the quality and quantity of incoming links. Based on this audit, we can help you to improve your architecture, improve the relevance of your content, and promote link-building activities.</p>
</main>

<footer class="abs footer">
  Copyright © 2012 Brightquill Hub, LLC<br>
  Privacy Policy &nbsp;|&nbsp; Terms and Conditions
</footer>

</body>
</html>
```